Bright Harbor Design

We need a web design for our startup company based in Zurich, Switzerland called Bright Harbor. We offer professional flirt and dating advice, self development with seminars and practical coachings.

The final website aims for two capital goals. First, it will contain text, pictures and video based content presenting and advertising our services. Furthermore, we want to bind our costumers with a plattform offering them to share their expiriences related with our services.

The targeted group will be men from 25 to 40 years.
Updates

The design requires also a register-box to put in the clients Name and Email

I need (besides of the "email registration box") a "Video Gallery", "Blog" and "Agenda (with the next events to come)"

Reason: I want to make a poll now

Target Market(s)

Guys around 25 to 40 years who want to improve their social lifestyle

Industry/Entity Type

Advertising

Requirements
Must have
• First and foremost, the design must transfer strong emotions and suggest an attractive social lifestyle.

The design should not be overloaded with content but should include pictures, videos and text.

The design should present a modern, urban lifestyle.
Nice to have
• There is a logo attached to the assignement. However, if you have a good idea for an improved or different logo, please do not hesitate to design your ideas.

```html
<!DOCTYPE html>
<html lang="en">
<head>
<meta charset="utf-8">
<title>Bright Harbor — Video Gallery, Agenda and Blog</title>
<link href="https://fonts.googleapis.com/css2?family=Open+Sans:wght@400;600;700&display=swap" rel="stylesheet">
<style>
:root{
  --green:#139a74;
  --green-dark:#0f8a67;
  --teal:#1e88a8;
  --heading:#666666;
  --body:#555555;
  --white:#ffffff;
  --sidebar:#f5f5f5;
  --band:#efefef;
  --footer:#898989;
  --footer-bottom:#4f4f4f;
  --field:#555555;
  --field-border:#3a3a3a;
  --player:#000000;
  --player-ctrl:#1b1b1b;
}
*{box-sizing:border-box;margin:0;padding:0}
html,body{width:1200px;height:946px;overflow:hidden}
body{position:relative;font-family:"Open Sans",Arial,sans-serif;background:var(--white);color:var(--body)}
.abs{position:absolute}
a{color:inherit;text-decoration:none}

.sidebar-bg{left:802px;top:0;width:398px;height:720px;background:var(--sidebar)}
.agenda-bg{left:0;top:397px;width:802px;height:323px;background:var(--band)}

.section-title{font-size:25px;font-weight:700;color:var(--heading);text-transform:uppercase;line-height:1;letter-spacing:.2px}
.section-link{display:flex;align-items:center;gap:8px;font-size:13px;font-weight:600;color:var(--green);line-height:1}
.section-link svg{fill:var(--teal)}

.item-title{font-size:15px;font-weight:700;color:var(--green);line-height:18px}
.item-text{font-size:13px;color:var(--body);line-height:15.5px}

.btn{display:flex;align-items:center;justify-content:center;width:80px;height:25px;border-radius:3px;background:var(--green);color:var(--white);font-size:12px;font-weight:600}

/* video player */
.player{width:299px;height:211px;background:var(--player)}
.player .action{position:absolute;right:9px;width:42px;height:32px;background:var(--player-ctrl);border-radius:3px;display:flex;flex-direction:column;align-items:center;justify-content:center;color:var(--white);font-size:7px;font-weight:700;gap:1px}
.player .action svg{fill:var(--white)}
.player .pause{position:absolute;left:9px;top:164px;width:60px;height:38px;background:var(--player-ctrl);border-radius:3px;display:flex;align-items:center;justify-content:center}
.player .bar{position:absolute;left:77px;top:170px;width:213px;height:32px;background:var(--player-ctrl);border-radius:3px}
.player .track{position:absolute;left:9px;top:11px;width:96px;height:10px;border:1px solid #9a9a9a}
.player .time{position:absolute;left:70px;top:163px;background:var(--white);color:#111;font-size:9px;padding:1px 3px;border-radius:1px;line-height:11px}
.player .vol{position:absolute;left:113px;top:11px;display:flex;gap:2px}
.player .vol i{display:block;width:2px;height:10px;background:#6b6b6b}
.player .vol i:first-child{background:#3aa6d8}
.player .hd{position:absolute;left:151px;top:8px;font-size:14px;font-weight:700;font-style:italic;color:#6b6b6b}
.player .full{position:absolute;left:185px;top:10px}

/* photos */
.photo-frame{background:var(--white);padding:3px}
.photo{width:100%;height:100%}

/* agenda date */
.date{width:125px;height:114px;background:var(--green);color:var(--white);text-align:center}
.date .day{font-size:44px;font-weight:600;line-height:1;padding-top:21px}
.date .month{font-size:18px;line-height:1;margin-top:12px}

/* footer */
.footer{left:0;top:720px;width:1200px;height:174px;background:var(--footer);color:var(--white)}
.footer-bottom{left:0;top:894px;width:1200px;height:52px;background:var(--footer-bottom);color:var(--white);font-size:12px;display:flex;align-items:center;justify-content:center}
.footer-title{font-size:15px;color:#f4f4f4;line-height:1}
.nav-link{font-size:13px;color:var(--white);line-height:1}
.field{width:188px;height:27px;background:var(--field);border:1px solid var(--field-border);border-radius:4px;color:var(--white);font-size:11px;padding:5px 9px;box-shadow:inset 0 1px 2px rgba(0,0,0,.3)}
.field.message{width:211px;height:65px}
.send{width:81px;height:29px;border-radius:4px;background:linear-gradient(#ffffff,#e6e6e6);border:1px solid #cfcfcf;color:var(--body);font-size:13px;display:flex;align-items:center;justify-content:center}
</style>
</head>
<body>

<div class="abs sidebar-bg"></div>
<div class="abs agenda-bg"></div>

<!-- Video gallery -->
<h2 class="abs section-title" style="left:131px;top:29px">Video Gallery</h2>
<a class="abs section-link" style="left:685px;top:34px" href="#">
  <svg width="18" height="13" viewBox="0 0 18 13"><circle cx="4" cy="3" r="2.6"/><circle cx="9.5" cy="3" r="2.6"/><rect x="0" y="6" width="13" height="7" rx="1"/><path d="M13 8.5 18 6v7l-5-2.5z"/></svg>
  All videos
</a>

<div class="abs player" style="left:131px;top:78px">
  <div class="action" style="top:8px"><svg width="14" height="12" viewBox="0 0 14 12"><path d="M7 12 1.2 6.2A3.3 3.3 0 0 1 7 2a3.3 3.3 0 0 1 5.8 4.2z"/></svg>LIKE</div>
  <div class="action" style="top:46px"><svg width="14" height="14" viewBox="0 0 14 14"><circle cx="7" cy="7" r="6" fill="none" stroke="#fff" stroke-width="1.6"/><path d="M7 3.5V7l2.5 1.8" fill="none" stroke="#fff" stroke-width="1.6"/></svg>LATER</div>
  <div class="action" style="top:84px"><svg width="16" height="12" viewBox="0 0 16 12"><circle cx="3" cy="9" r="1.5"/><circle cx="7" cy="6" r="1.5"/><circle cx="11" cy="3" r="1.5"/><path d="M11 0h5v5z"/></svg>SHARE</div>
  <div class="pause"><svg width="16" height="18" viewBox="0 0 16 18"><rect width="5" height="18" fill="#fff"/><rect x="11" width="5" height="18" fill="#fff"/></svg></div>
  <div class="bar">
    <div class="track"></div>
    <div class="vol"><i></i><i></i><i></i><i></i><i></i><i></i><i></i><i></i></div>
    <div class="hd">HD</div>
    <svg class="full" width="12" height="12" viewBox="0 0 12 12" fill="none" stroke="#fff" stroke-width="2"><path d="M1 1l4 4M11 1 7 5M1 11l4-4M11 11 7 7"/></svg>
  </div>
  <div class="time">00:00</div>
</div>
<h3 class="abs item-title" style="left:131px;top:308px">Most important self development rules</h3>
<p class="abs item-text" style="left:131px;top:337px;width:305px">Proin gravida nibh vel velit auctor aliquet. Aenean sollicitudin, lorem quis bibendum auctor.</p>

<div class="abs player" style="left:470px;top:78px">
  <div class="action" style="top:8px"><svg width="14" height="12" viewBox="0 0 14 12"><path d="M7 12 1.2 6.2A3.3 3.3 0 0 1 7 2a3.3 3.3 0 0 1 5.8 4.2z"/></svg>LIKE</div>
  <div class="action" style="top:46px"><svg width="14" height="14" viewBox="0 0 14 14"><circle cx="7" cy="7" r="6" fill="none" stroke="#fff" stroke-width="1.6"/><path d="M7 3.5V7l2.5 1.8" fill="none" stroke="#fff" stroke-width="1.6"/></svg>LATER</div>
  <div class="action" style="top:84px"><svg width="16" height="12" viewBox="0 0 16 12"><circle cx="3" cy="9" r="1.5"/><circle cx="7" cy="6" r="1.5"/><circle cx="11" cy="3" r="1.5"/><path d="M11 0h5v5z"/></svg>SHARE</div>
  <div class="pause"><svg width="16" height="18" viewBox="0 0 16 18"><rect width="5" height="18" fill="#fff"/><rect x="11" width="5" height="18" fill="#fff"/></svg></div>
  <div class="bar">
    <div class="track"></div>
    <div class="vol"><i></i><i></i><i></i><i></i><i></i><i></i><i></i><i></i></div>
    <div class="hd">HD</div>
    <svg class="full" width="12" height="12" viewBox="0 0 12 12" fill="none" stroke="#fff" stroke-width="2"><path d="M1 1l4 4M11 1 7 5M1 11l4-4M11 11 7 7"/></svg>
  </div>
  <div class="time">00:00</div>
</div>
<h3 class="abs item-title" style="left:470px;top:308px">20 dating advices for smooth dates</h3>
<p class="abs item-text" style="left:470px;top:337px;width:300px">Proin gravida nibh vel velit auctor aliquet lorem. Aenean sollicitudin, lorem quis.</p>

<!-- Blog -->
<h2 class="abs section-title" style="left:830px;top:29px">Blog</h2>
<a class="abs section-link" style="left:994px;top:34px" href="#">
  <svg width="15" height="13" viewBox="0 0 15 13"><path d="M7.5 0C11.6 0 15 2.5 15 5.6s-3.4 5.6-7.5 5.6c-.8 0-1.5-.1-2.2-.3L1.5 13l1-3.1C.9 8.9 0 7.3 0 5.6 0 2.5 3.4 0 7.5 0z"/></svg>
  All posts
</a>

<div class="abs photo-frame" style="left:830px;top:78px;width:240px;height:141px">
  <div class="photo" role="img" aria-label="Photo: a man and a woman chatting in a warmly lit market shop" style="background:linear-gradient(120deg,#5a3a22,#8a5a34 40%,#3e2a3a 70%,#6b4a2e)"></div>
</div>
<h3 class="abs item-title" style="left:830px;top:236px;width:240px">10 reason why you should flirt with women</h3>
<p class="abs item-text" style="left:830px;top:283px;width:225px">Proin gravida nibh vel velit auctor aliquet. Aenean sollicitudin, lorem quis bibendum auctor.</p>
<a class="abs btn" style="left:990px;top:342px" href="#">Read more</a>

<div class="abs photo-frame" style="left:830px;top:397px;width:240px;height:141px">
  <div class="photo" role="img" aria-label="Photo: a man and a woman talking on a city street in winter" style="background:linear-gradient(120deg,#4a4c50,#7a7c80 45%,#5c5a58 70%,#8e8a86)"></div>
</div>
<h3 class="abs item-title" style="left:830px;top:555px;width:200px">Most important self development rules</h3>
<p class="abs item-text" style="left:830px;top:602px;width:225px">Proin gravida nibh vel velit auctor aliquet. Aenean sollicitudin, lorem quis bibendum auctor.</p>
<a class="abs btn" style="left:990px;top:661px" href="#">Read more</a>

<!-- Agenda -->
<h2 class="abs section-title" style="left:131px;top:420px">Agenda</h2>
<a class="abs section-link" style="left:685px;top:423px" href="#">
  <svg width="16" height="15" viewBox="0 0 16 15"><path d="M8 0l2.4 5 5.6.6-4.2 3.8 1.2 5.6L8 12.2 3 15l1.2-5.6L0 5.6 5.6 5z"/></svg>
  All events
</a>

<div class="abs date" style="left:131px;top:464px"><div class="day">5</div><div class="month">MAY</div></div>
<div class="abs photo" role="img" aria-label="Photo: a smiling couple piggybacking on a sunny beach" style="left:256px;top:464px;width:173px;height:114px;background:linear-gradient(120deg,#2e5a7a,#8fb6c8 45%,#c8b49a 75%,#e2d6c4)"></div>
<h3 class="abs item-title" style="left:131px;top:593px">Most important self development rules</h3>
<p class="abs item-text" style="left:131px;top:623px;width:300px">Proin gravida nibh vel velit auctor aliquet.Aenean sollicitudin, lorem quis bibendum auctor. Dorem quis bibendum auctor.</p>
<a class="abs btn" style="left:350px;top:679px" href="#">Read more</a>

<div class="abs date" style="left:473px;top:464px"><div class="day">23</div><div class="month">MAY</div></div>
<div class="abs photo" role="img" aria-label="Photo: a young couple sitting together outdoors and laughing" style="left:598px;top:464px;width:173px;height:114px;background:linear-gradient(120deg,#4a3a2e,#8a6a50 45%,#6a7890 70%,#b0a090)"></div>
<h3 class="abs item-title" style="left:473px;top:593px">Most important self development rules</h3>
<p class="abs item-text" style="left:473px;top:623px;width:300px">Proin gravida nibh vel velit auctor aliquet.Aenean sollicitudin, lorem quis bibendum auctor. Dorem quis bibendum auctor.</p>
<a class="abs btn" style="left:691px;top:679px" href="#">Read more</a>

<!-- Footer -->
<footer class="abs footer">
  <h4 class="abs footer-title" style="left:131px;top:21px">Navigation</h4>
  <a class="abs nav-link" style="left:131px;top:62px" href="#">Services</a>
  <a class="abs nav-link" style="left:131px;top:92px" href="#">About Us</a>
  <a class="abs nav-link" style="left:131px;top:122px" href="#">Agenda</a>
  <a class="abs nav-link" style="left:212px;top:62px;text-decoration:underline" href="#">Video Gallery</a>
  <a class="abs nav-link" style="left:212px;top:92px" href="#">Blog</a>
  <a class="abs nav-link" style="left:212px;top:122px" href="#">Contacts</a>

  <h4 class="abs footer-title" style="left:370px;top:21px">Contacts</h4>
  <svg class="abs" style="left:375px;top:66px" width="14" height="22" viewBox="0 0 14 22"><rect x="1" y="1" width="12" height="20" rx="2" fill="none" stroke="#4a4a4a" stroke-width="2"/><rect x="3" y="4" width="8" height="11" fill="#4a4a4a"/><circle cx="7" cy="18" r="1.2" fill="#4a4a4a"/></svg>
  <span class="abs nav-link" style="left:407px;top:70px">555 014 2270</span>
  <svg class="abs" style="left:371px;top:116px" width="23" height="15" viewBox="0 0 23 15" fill="none" stroke="#4a4a4a" stroke-width="1.5"><rect x=".75" y=".75" width="21.5" height="13.5"/><path d="M1 1l10.5 8L22 1M1 14l8-6.5M22 14l-8-6.5"/></svg>
  <a class="abs nav-link" style="left:407px;top:114px;text-decoration:underline" href="#">info@brightharbor-mail.com</a>

  <h4 class="abs footer-title" style="left:615px;top:21px">Send us a message</h4>
  <div class="abs field" style="left:611px;top:48px">Name</div>
  <div class="abs field" style="left:611px;top:87px">E-Mail</div>
  <div class="abs field" style="left:611px;top:126px">Subject</div>
  <div class="abs field message" style="left:814px;top:48px">Your message</div>
  <div class="abs send" style="left:945px;top:125px">Send</div>
</footer>
<div class="abs footer-bottom">All right reserved © Bright Harbor 2013</div>

</body>
</html>
```